Business Card Design for a Personal Trainer

I need a business card design for my job as a personal trainer. It should have a unique, modern and exclusive design. On the front there should be only my logo with my name and my job. 0162/3819204 Tobias Lendhart Wiesengrundweg 14 80417 Munich Germany The most important contact information is the web adress. it can be bigger than the rest, but its not necessary. The card should be 8,5cmx5,5cm big. Font: Roboto. Colors: black, white, gray, 56c1ff.

```html
<!DOCTYPE html>
<html lang="de">
<head>
<meta charset="utf-8">
<title>Tobias Lendhart – Personal Trainer Visitenkarte</title>
<link rel="stylesheet" href="https://fonts.googleapis.com/css2?family=Roboto:wght@300;400;500&display=swap">
<style>
  :root {
    --page-bg: #d6d6d6;
    --card-bg: #2b2a2b;
    --brand-gray: #8f8f8f;
    --text-white: #ffffff;
    --highlight-bg: #8a8a8a;
    --photo-dark: #1e1e1f;
    --photo-light: #6b6b6b;
  }
  * { margin: 0; padding: 0; box-sizing: border-box; }
  html, body {
    width: 1200px;
    height: 1200px;
    overflow: hidden;
    background: var(--page-bg);
    font-family: "Roboto", Arial, sans-serif;
  }
  .card {
    position: absolute;
    left: 219px;
    width: 762px;
    height: 492px;
    background: var(--card-bg);
  }
  .card--front { top: 91px; }
  .card--back { top: 616px; }

  /* Front */
  .brand-mark {
    position: absolute;
    left: 351px;
    top: 200px;
    width: 60px;
    height: 60px;
    background: var(--brand-gray);
  }
  .brand-name {
    position: absolute;
    left: 0;
    width: 100%;
    top: 286px;
    text-align: center;
    font-weight: 400;
    font-size: 56px;
    line-height: 1;
    color: var(--brand-gray);
    letter-spacing: 1px;
  }
  .brand-role {
    position: absolute;
    top: 366px;
    left: 105px;
    width: 552px;
    display: flex;
    align-items: center;
    gap: 10px;
    color: var(--brand-gray);
    font-size: 22px;
    font-weight: 400;
    letter-spacing: 4px;
  }
  .brand-role::before,
  .brand-role::after {
    content: "";
    flex: 1;
    height: 2px;
    background: var(--brand-gray);
  }

  /* Back */
  .portrait {
    position: absolute;
    left: 45px;
    top: 52px;
    width: 256px;
    height: 440px;
    border-radius: 110px 110px 0 0;
    background: radial-gradient(ellipse at 50% 40%, var(--photo-light), var(--photo-dark) 75%);
  }
  .contact {
    position: absolute;
    left: 331px;
    top: 188px;
    list-style: none;
    color: var(--text-white);
    font-size: 21px;
    font-weight: 400;
    letter-spacing: 3.4px;
    line-height: 37.6px;
  }
  .contact__web {
    display: inline-block;
    background: var(--highlight-bg);
    font-weight: 500;
    padding: 0 4px;
    line-height: 30px;
    margin-bottom: 4px;
  }
</style>
</head>
<body>
  <section class="card card--front" aria-label="Vorderseite">
    <div class="brand-mark"></div>
    <h1 class="brand-name">TOBIAS LENDHART</h1>
    <p class="brand-role">PERSONAL TRAINER</p>
  </section>

  <section class="card card--back" aria-label="Rückseite">
    <div class="portrait" role="img" aria-label="Schwarzweiß-Porträt des Trainers mit verschränkten Armen"></div>
    <ul class="contact">
      <li><span class="contact__web">www.tobiaslendhart.de</span></li>
      <li>t.lendhart@postfach-mail.de</li>
      <li>0162/3819204</li>
      <li>Tobias Lendhart</li>
      <li>Wiesengrundweg 14</li>
      <li>80417 München</li>
    </ul>
  </section>
</body>
</html>
```